Business Card Design

We have recently seen two business cards that caught our attention and think the designs would work for us. We are an accounting firm that serves small businesses in a variety of industries. Attached are the two business card that inspired us along with very rough layouts. We would like to see a professional layout using our company information.

Industry/Entity Type

Accounting

Contact Information for Business Card

Company Name - Marlowe Thistle
Address - 4182 Orlanby Lane, Suite 610, Houston, TX 77093
713-555-0187 - Main
281-555-0342 - Fax

Team Member Names, emails and phone numbers (see attachment)

```html
<!DOCTYPE html>
<html lang="en">
<head>
<meta charset="utf-8">
<title>Marlowe Thistle – Business Cards</title>
<link rel="stylesheet" href="https://fonts.googleapis.com/css2?family=Cinzel:wght@500;600&family=Exo+2:wght@400;500&display=swap">
<style>
  :root {
    --page: #e9e7e4;
    --card-white: #ffffff;
    --card-soft: #e4e4e4;
    --charcoal: #363636;
    --swoosh: #b4b4b4;
    --swoosh-light: #d2d2d2;
    --ink: #2e2e2e;
    --on-dark: #f2f2f2;
    --muted-on-dark: #cfcfcf;
  }
  * { box-sizing: border-box; margin: 0; padding: 0; }
  html, body { width: 1200px; height: 899px; overflow: hidden; }
  body {
    background: var(--page);
    display: flex;
    align-items: center;
    justify-content: center;
    gap: 48px;
    font-family: "Exo 2", sans-serif;
  }
  .card {
    position: relative;
    width: 520px;
    height: 297px;
    background: radial-gradient(ellipse at 55% 35%, var(--card-white) 0%, var(--card-white) 35%, var(--card-soft) 100%);
    box-shadow: 0 6px 18px rgba(0,0,0,0.18);
    overflow: hidden;
  }
  .brand-name {
    font-family: "Cinzel", serif;
    font-weight: 600;
    color: var(--ink);
    letter-spacing: 1px;
    white-space: nowrap;
  }
  /* Front */
  .card-front .brand {
    position: absolute;
    left: 0; right: 0; top: 108px;
    display: flex; flex-direction: column; align-items: center; gap: 14px;
  }
  .brand-mark {
    width: 34px; height: 34px;
    background: var(--charcoal);
  }
  .card-front .brand-name { font-size: 28px; }
  .web-tab {
    position: absolute;
    right: 0; bottom: 0;
    width: 232px; height: 30px;
    background: var(--charcoal);
    border-top-left-radius: 16px;
    color: var(--on-dark);
    font-size: 12px;
    letter-spacing: 2px;
    display: flex; align-items: center; justify-content: center;
  }
  /* Back */
  .card-back .backdrop { position: absolute; inset: 0; width: 100%; height: 100%; }
  .card-back .brand-name {
    position: absolute; left: 30px; top: 70px; font-size: 27px;
  }
  .holder {
    position: absolute; left: 26px; bottom: 52px; color: var(--on-dark);
  }
  .holder-name { font-size: 16px; font-weight: 500; letter-spacing: 1.5px; text-transform: uppercase; }
  .holder-title { font-size: 10.5px; letter-spacing: 1px; text-transform: uppercase; color: var(--muted-on-dark); margin-top: 2px; }
  .office-address {
    position: absolute; left: 26px; bottom: 18px;
    font-size: 10.5px; letter-spacing: 0.8px; color: var(--on-dark);
  }
  .contact-list {
    position: absolute; right: 22px; top: 150px;
    list-style: none; color: var(--on-dark);
    font-size: 12px; letter-spacing: 1px;
  }
  .contact-list li { display: flex; align-items: center; gap: 8px; height: 21px; }
  .contact-list svg { width: 12px; height: 12px; fill: var(--on-dark); flex: none; }
</style>
</head>
<body>

  <section class="card card-front" aria-label="Business card front">
    <div class="brand">
      <span class="brand-mark"></span>
      <span class="brand-name">Marlowe Thistle</span>
    </div>
    <div class="web-tab">www.marlowethistle.com</div>
  </section>

  <section class="card card-back" aria-label="Business card back">
    <svg class="backdrop" viewBox="0 0 520 297" preserveAspectRatio="none" aria-hidden="true">
      <path d="M0,166 C200,170 380,124 520,4 L520,297 L0,297 Z" fill="var(--swoosh-light)"/>
      <path d="M0,176 C200,180 380,134 520,14 L520,297 L0,297 Z" fill="var(--swoosh)"/>
      <path d="M0,184 C200,188 380,142 520,22 L520,297 L0,297 Z" fill="var(--card-white)"/>
      <path d="M0,192 C200,196 380,150 520,30 L520,297 L0,297 Z" fill="var(--charcoal)"/>
    </svg>

    <span class="brand-name">Marlowe Thistle</span>

    <ul class="contact-list">
      <li><svg viewBox="0 0 12 12"><path d="M2.5 0.5 L4.5 3 L3.4 4.3 C4 5.8 6.2 8 7.7 8.6 L9 7.5 L11.5 9.5 L10 11.5 C5 11.5 0.5 7 0.5 2 Z"/></svg>713-555-0187</li>
      <li><svg viewBox="0 0 12 12"><path d="M3 0 H9 V12 H3 Z M4 1.5 V9.5 H8 V1.5 Z" fill-rule="evenodd"/></svg>713-555-0129</li>
      <li><svg viewBox="0 0 12 12"><path d="M3 0 H8 V3 H11 V11 H1 V3 H3 Z M4 1 V5 H7 V1 Z M3 7 H9 V9 H3 Z" fill-rule="evenodd"/></svg>281-555-0342</li>
      <li><svg viewBox="0 0 12 12"><path d="M0 2 H12 V10 H0 Z M1 3 L6 7 L11 3 Z" fill-rule="evenodd"/></svg>info@thistlemail.com</li>
      <li><svg viewBox="0 0 12 12"><path d="M6 0 A6 6 0 1 0 6 12 A6 6 0 1 0 6 0 Z M6 1 A5 5 0 1 1 6 11 A5 5 0 1 1 6 1 Z M5.5 1 H6.5 V11 H5.5 Z M1 5.5 H11 V6.5 H1 Z" fill-rule="evenodd"/></svg>www.marlowethistle.com</li>
    </ul>

    <div class="holder">
      <div class="holder-name">Dorian Vale</div>
      <div class="holder-title">Financial Advisor</div>
    </div>
    <div class="office-address">4182 Orlanby Lane, Suite 610, Houston</div>
  </section>

</body>
</html>
```